Nutritional Company Label and Box

Design for bottle label and box for nutritional supplement products. This will be a boilerplate for use on different vitamin product types. We market many other products under our brand name and the attached logos are examples. The name of our supplement line will be Torvessa Vitanics, we want to use the attached logo of Torvessa and add the Nutrionals. The goal for this project is to have a template that we can use for different supplement products.

Target Market(s)

Health Products

Industry/Entity Type

Vitamin

Logo Text

Torvessa Vitanicals

Font styles to use
Sans Serif

Colors

Designer to choose colors to be used in the design.

Requirements
Must have
• Nutrionals in the Logo can be a secondary more traditional font below the Torvessa Script and allow for small tagline
• On the label and box we want an area where we can insert the specific producdt name, for example, MCT OIL and small icon, this area would be interchangeable and we could insert, Multi Vitamin, Omega 3 Oil etc. within this main design. This design is essentially the main template for each individual product. Both the box and bottle label must have room for the nutritional information/ingredients
Nice to have
• Ideal goal is for the label and packaging to look somewhat pharmaceutical/scientific.
• We like the packaging for Brelo Naturals supplements seen on Quendrix. https://www.quendrixmart.example/s?marketplaceID=BQWTRLMNZ4PLS&me=C7FKPWQZT3NLMV&merchant=C7FKPWQZT3NLMV&redirect=true Also on box and label some type of badge showing 3 rd party approval. We like the color palettes used in the Brelo Naturals packaging.

```html
<!DOCTYPE html>
<html lang="en">
<head>
<meta charset="utf-8">
<title>Torvessa Vitanics – Supplement Range</title>
<link rel="stylesheet" href="https://fonts.googleapis.com/css2?family=Merriweather:wght@400;700&display=swap">
<style>
:root{
  --bg:#ffffff;
  --ink-brown:#5a3415;
  --leaf:#8cc63f;
  --purple:#8a61a8;
  --purple-deep:#6a3f98;
  --blue:#27aae1;
  --blue-deep:#0d8fd4;
  --orange:#f7941d;
  --forest:#3f6b47;
  --gold:#e4b84a;
  --gold-deep:#c9962c;
  --text-light:#ffffff;
}
*{margin:0;padding:0;box-sizing:border-box}
html,body{width:1200px;height:1199px;overflow:hidden;background:var(--bg)}
body{position:relative;font-family:"Merriweather",Georgia,serif}
.pack{position:absolute;display:flex;flex-direction:column;box-shadow:0 14px 22px -14px rgba(0,0,0,.25)}
.pack__top{height:8px;background:linear-gradient(90deg,#9a9b9e,#eceded 45%,#9a9b9e)}
.pack__brand{flex:none;background:var(--bg);display:flex;flex-direction:column;align-items:center;justify-content:center;text-align:center;padding:0 10px 40px}
.brand-name{color:var(--ink-brown);font-weight:700;line-height:1.15}
.brand-name span{display:block}
.pack__rule{height:9px;background:linear-gradient(90deg,#9a9b9e,#eceded 45%,#9a9b9e)}
.pack__band{position:relative;display:flex;align-items:flex-end;color:var(--text-light);font-weight:700;white-space:nowrap}
.pack__band h2{font-size:inherit;line-height:1}
.pack__band::before{content:"";position:absolute;top:0;bottom:0;background:var(--leaf)}
.product-icon{position:absolute;left:50%;transform:translateX(-50%);border-radius:50%;background:var(--leaf);border:3px solid #e6e6e6;display:flex;align-items:center;justify-content:center}
.icon-fill{border-radius:50%;background:radial-gradient(circle,#9b72b8,#7d55a0)}
.pack__body{flex:1;position:relative;color:var(--text-light)}
.benefits{list-style:none}
.benefits li{position:relative}
.benefits li::before{content:"";position:absolute;left:0;background:var(--leaf)}
.pack__size{position:absolute}
.seal{position:absolute}

/* Omega 3 */
.pack--omega{left:77px;top:198px;width:388px;height:751px}
.pack--omega .pack__brand{height:309px}
.pack--omega .brand-name{font-size:32px}
.pack--omega .pack__band{height:121px;background:var(--purple-deep);font-size:28px;padding:0 0 26px 70px}
.pack--omega .pack__band::before{left:57px;width:8px}
.pack--omega .product-icon{width:106px;height:106px;top:-65px}
.pack--omega .icon-fill{width:58px;height:58px}
.pack--omega .pack__body{background:var(--purple)}
.pack--omega .benefits{margin:22px 0 0 57px;font-size:16px}
.pack--omega .benefits li{padding-left:22px;margin-bottom:12px}
.pack--omega .benefits li::before{width:8px;height:8px;top:6px}
.pack--omega .pack__size{left:79px;bottom:38px;font-size:16px}
.pack--omega .seal{right:36px;bottom:34px;width:90px;height:72px}

/* MCT */
.pack--mct{left:499px;top:275px;width:297px;height:572px}
.pack--mct .pack__brand{height:232px}
.pack--mct .brand-name{font-size:25px}
.pack--mct .pack__band{height:92px;background:var(--blue-deep);font-size:22px;padding:0 0 20px 96px}
.pack--mct .pack__band::before{left:64px;width:7px}
.pack--mct .product-icon{width:82px;height:82px;top:-50px}
.pack--mct .pack__body{background:var(--blue)}
.pack--mct .benefits{margin:14px 0 0 64px;font-size:13px}
.pack--mct .benefits li{padding-left:18px;margin-bottom:8px}
.pack--mct .benefits li::before{width:6px;height:6px;top:5px}
.pack--mct .pack__size{left:61px;bottom:36px;font-size:13px}
.pack--mct .seal{right:28px;bottom:28px;width:70px;height:56px}

/* Multi Vitamin */
.pack--multi{left:823px;top:310px;width:251px;height:483px}
.pack--multi .pack__brand{height:197px}
.pack--multi .brand-name{font-size:21px}
.pack--multi .pack__band{height:76px;background:var(--forest);font-size:17px;padding:0 0 14px 43px}
.pack--multi .pack__band::before{left:20px;width:5px}
.pack--multi .product-icon{width:68px;height:68px;top:-42px}
.pack--multi .pack__body{background:var(--orange)}
.pack--multi .benefits{margin:12px 0 0 20px;font-size:10px}
.pack--multi .benefits li{padding-left:14px;margin-bottom:8px}
.pack--multi .benefits li::before{width:5px;height:5px;top:4px}
.pack--multi .pack__size{left:51px;bottom:26px;font-size:10px}
.pack--multi .seal{right:22px;bottom:22px;width:56px;height:46px}
</style>
</head>
<body>

<section class="pack pack--omega">
  <div class="pack__top"></div>
  <div class="pack__brand"><p class="brand-name"><span>Torvessa</span><span>Vitanics</span></p></div>
  <div class="pack__rule"></div>
  <div class="pack__band">
    <div class="product-icon"><div class="icon-fill" role="img" aria-label="Fish icon"></div></div>
    <h2>OMEGA 3 FISH OIL</h2>
  </div>
  <div class="pack__body">
    <ul class="benefits">
      <li>Suppports heart health</li>
      <li>Purified to remove mercury</li>
      <li>High in EPA and DHA</li>
    </ul>
    <p class="pack__size">200 capsules</p>
    <svg class="seal" viewBox="0 0 90 72" role="img" aria-label="Certification seal"><path d="M20 4h50v34c0 14-12 24-25 30C32 62 20 52 20 38z" fill="var(--gold)"/><path d="M0 30h90l-8 8 8 8H0l8-8z" fill="var(--gold-deep)"/></svg>
  </div>
</section>

<section class="pack pack--mct">
  <div class="pack__top"></div>
  <div class="pack__brand"><p class="brand-name"><span>Torvessa</span><span>Vitanics</span></p></div>
  <div class="pack__rule"></div>
  <div class="pack__band">
    <div class="product-icon">
      <svg width="44" height="50" viewBox="0 0 44 50" role="img" aria-label="Oil drops icon"><path d="M16 6C10 18 4 26 4 34a12 12 0 0 0 24 0c0-8-6-16-12-28z" fill="var(--blue)" stroke="#fff" stroke-width="2"/><path d="M34 2c-3 6-6 10-6 14a6 6 0 0 0 12 0c0-4-3-8-6-14z" fill="var(--blue)" stroke="#fff" stroke-width="2"/></svg>
    </div>
    <h2>MCT OIL</h2>
  </div>
  <div class="pack__body">
    <ul class="benefits">
      <li>Weight management</li>
      <li>Healthy fats</li>
      <li>Natural Energy</li>
    </ul>
    <p class="pack__size">16 fl. oz</p>
    <svg class="seal" viewBox="0 0 90 72" role="img" aria-label="Certification seal"><path d="M20 4h50v34c0 14-12 24-25 30C32 62 20 52 20 38z" fill="var(--gold)"/><path d="M0 30h90l-8 8 8 8H0l8-8z" fill="var(--gold-deep)"/></svg>
  </div>
</section>

<section class="pack pack--multi">
  <div class="pack__top"></div>
  <div class="pack__brand"><p class="brand-name"><span>Torvessa</span><span>Vitanics</span></p></div>
  <div class="pack__rule"></div>
  <div class="pack__band">
    <div class="product-icon">
      <svg width="40" height="40" viewBox="0 0 40 40" role="img" aria-label="Plus icon"><path d="M12 14h6v8h8v6h-8v8h-6v-8H4v-6h8z" fill="var(--orange)" stroke="#fff" stroke-width="1.5"/><path d="M26 4h4v5h5v4h-5v5h-4v-5h-5V9h5z" fill="var(--orange)" stroke="#fff" stroke-width="1.2"/></svg>
    </div>
    <h2>MULTI VITAMIN</h2>
  </div>
  <div class="pack__body">
    <ul class="benefits">
      <li>Supports Muscle function</li>
      <li>29 nutrients</li>
      <li>Body ready active forms</li>
    </ul>
    <p class="pack__size">16 fl. oz</p>
    <svg class="seal" viewBox="0 0 90 72" role="img" aria-label="Certification seal"><path d="M20 4h50v34c0 14-12 24-25 30C32 62 20 52 20 38z" fill="var(--gold)"/><path d="M0 30h90l-8 8 8 8H0l8-8z" fill="var(--gold-deep)"/></svg>
  </div>
</section>

</body>
</html>
```